Copperleaf Roofing Business Card

This is my current business card. But I’d like to make some changes. Somewhere on the card I’d like to list some of the services we offer. Maybe on the back? But I’d still like to keep the red. White and black modern look.

-residential & commercial roofing
-Roof Repairs & Maintenance
-Storm Damage & Insurance Claims specialist
-Christmas Lights and permanent Christmas lights
Fencing. Windows. Gutters. Siding. Sheetrock, painting.

```html
<!DOCTYPE html>
<html lang="en">
<head>
<meta charset="utf-8">
<title>Copperleaf Roofing Business Card</title>
<link href="https://fonts.googleapis.com/css2?family=Audiowide&family=Arimo:wght@400;700&display=swap" rel="stylesheet">
<style>
  :root {
    --bg: #d9d9dc;
    --red: #e3202a;
    --red-deep: #8f1016;
    --black: #070707;
    --white: #ffffff;
    --grey-text: #e6e6e6;
  }
  * { box-sizing: border-box; margin: 0; padding: 0; }
  html, body { width: 1200px; height: 800px; overflow: hidden; }
  body {
    background: var(--bg);
    font-family: "Arimo", Arial, sans-serif;
    display: flex;
    align-items: center;
    justify-content: center;
    gap: 40px;
  }
  .card {
    position: relative;
    width: 520px;
    height: 297px;
    border-radius: 4px;
    overflow: hidden;
    box-shadow: 0 10px 24px rgba(0,0,0,0.22);
  }

  /* Front */
  .card-front { display: flex; align-items: center; justify-content: center; }
  .tartan-fill {
    position: absolute; inset: 0;
    background: linear-gradient(135deg, var(--red) 0%, var(--red-deep) 45%, #2a0608 70%, var(--red) 100%);
  }
  .front-brand {
    position: relative;
    font-family: "Arimo", Arial, sans-serif;
    font-weight: 700;
    color: var(--white);
    font-size: 30px;
    letter-spacing: 0.5px;
    white-space: nowrap;
  }

  /* Back */
  .card-back { background: var(--black); color: var(--white); }
  .back-band {
    position: absolute; left: 0; right: 0; bottom: 0; height: 34px;
    background: linear-gradient(90deg, var(--red-deep), var(--red) 50%, var(--red-deep));
  }
  .owner { position: absolute; left: 28px; top: 40px; }
  .owner-name {
    font-family: "Audiowide", sans-serif;
    color: var(--red);
    font-size: 22px;
    font-weight: 400;
    text-transform: uppercase;
    letter-spacing: 1px;
  }
  .owner-title { font-size: 13px; color: var(--grey-text); margin-top: 2px; }
  .contact-list { list-style: none; margin-top: 16px; }
  .contact-list li {
    display: flex; align-items: center; gap: 8px;
    font-size: 13px; color: var(--grey-text); margin-bottom: 6px;
  }
  .contact-list svg { width: 12px; height: 12px; fill: var(--red); flex: none; }

  .back-brand {
    position: absolute; right: 28px; top: 92px;
    font-family: "Arimo", Arial, sans-serif;
    font-weight: 700;
    color: var(--white);
    font-size: 18px;
    white-space: nowrap;
  }

  .services { position: absolute; right: 28px; top: 142px; text-align: right; }
  .services-title {
    font-size: 15px; font-weight: 700; color: var(--red);
    letter-spacing: 0.5px; margin-bottom: 6px;
  }
  .service-list { list-style: none; }
  .service-list li {
    display: flex; justify-content: flex-end; align-items: center; gap: 5px;
    font-size: 11.5px; color: var(--grey-text); margin-bottom: 3px;
  }
  .service-list svg { width: 9px; height: 9px; stroke: var(--red); fill: none; stroke-width: 2.4; flex: none; }
</style>
</head>
<body>

  <section class="card card-front">
    <div class="tartan-fill" role="img" aria-label="Red, black and white tartan plaid pattern"></div>
    <p class="front-brand">Copperleaf Roofing</p>
  </section>

  <section class="card card-back">
    <div class="owner">
      <h1 class="owner-name">Dale Mercer</h1>
      <p class="owner-title">OWNER</p>
      <ul class="contact-list">
        <li><svg viewBox="0 0 24 24"><path d="M6.6 10.8a15 15 0 0 0 6.6 6.6l2.2-2.2c.3-.3.7-.4 1-.2 1.1.4 2.3.6 3.6.6.6 0 1 .4 1 1V20c0 .6-.4 1-1 1A17 17 0 0 1 3 4c0-.6.4-1 1-1h3.5c.6 0 1 .4 1 1 0 1.3.2 2.5.6 3.6.1.3 0 .7-.2 1z"/></svg>555-014-2290</li>
        <li><svg viewBox="0 0 24 24"><path d="M2 5h20v14H2zm2 2v.5l8 5 8-5V7l-8 5z"/></svg>dale@copperleafroofing.co</li>
        <li><svg viewBox="0 0 24 24"><path d="M12 2a10 10 0 1 0 0 20 10 10 0 0 0 0-20zm0 2c.8 1.2 1.4 2.5 1.8 4h-3.6c.4-1.5 1-2.8 1.8-4zM4.3 14a8 8 0 0 1 0-4h3.4a16 16 0 0 0 0 4zM12 20c-.8-1.2-1.4-2.5-1.8-4h3.6c-.4 1.5-1 2.8-1.8 4zm2.3-6H9.7a14 14 0 0 1 0-4h4.6a14 14 0 0 1 0 4zm2 0a16 16 0 0 0 0-4h3.4a8 8 0 0 1 0 4z"/></svg>www.copperleafroofing.co</li>
      </ul>
    </div>

    <p class="back-brand">Copperleaf Roofing</p>

    <div class="services">
      <h2 class="services-title">SERVICES</h2>
      <ul class="service-list">
        <li>Residential &amp; Commercial Roofing<svg viewBox="0 0 10 10"><path d="M1 5l3 3 5-6"/></svg></li>
        <li>Roof Repairs &amp; Maintenance<svg viewBox="0 0 10 10"><path d="M1 5l3 3 5-6"/></svg></li>
        <li>Storm Damage &amp; Insurance Claims Specialist<svg viewBox="0 0 10 10"><path d="M1 5l3 3 5-6"/></svg></li>
        <li>Christmas Lights And Permanent Christmas Lights<svg viewBox="0 0 10 10"><path d="M1 5l3 3 5-6"/></svg></li>
        <li>Fencing, Windows, Gutters<svg viewBox="0 0 10 10"><path d="M1 5l3 3 5-6"/></svg></li>
        <li>Siding, Sheetrock, painting<svg viewBox="0 0 10 10"><path d="M1 5l3 3 5-6"/></svg></li>
      </ul>
    </div>

    <div class="back-band" role="img" aria-label="Strip of red and black tartan plaid pattern"></div>
  </section>

</body>
</html>
```